Web design for Crowdfunding site HopeWingsRally.com

We need a web design for christian crowdfunding website. Here is the challenge: We need responsive layout that is targeted first in iPad size of screen. It should also scale somehow down to iPhone size of screens. Web layout can be about the same size as iPad screen.

Screens should work so that main page scrolls not but only certain part of the screen scrolls and always one "page" at time. We can implement these "scrolls" then later with javascript but now we need only design. The challenge is to create this kind of hybrid website / app look.

Target is at first to raise funds to orphan people needing about $40 per month for their living and education. There is always some organization which takes care of these kids. Later there will be other christian missions included. At first we are looking to find monthly supporters.

You can be as creative as you want :) As you see from the look and feel sector, I am not looking any same traditional look which many "help kids" sites have. I am looking to reach now younger generation and therefore iPad and mobile are the main screen sizes.

Inspirational designs:
- https://example-gallery.test/profiles/studiofernlake/designs/482716?from=%2Fbrowse%2Fxhr%2Fdesigns%3Fcategory%3Dmobile-app-design
- http://www.artpoolhub.test/design/8261047 Clear, simple visuals
- http://www.artpoolhub.test/design/7394215 Header
- http://www.artpoolhub.test/design/6048392 Contrast in the colors, i think is powerfull

Some terms could be: Kids play, kids are learning (in the school). No static posture but living like kids are. I wonder also how we could also add little bit gaming style even though the question is of reali life of real people. Giving should be rewarding.

Target Market(s)

People who want help other people.

Industry/Entity Type

Christian

Number of Pages Required

4 page

Requirements
Must have
• Homepage. Mission page (In my wireframes it was one kid).
Nice to have
• Other pages and some idea how to scroll. 4 pages is no must. If you feel easy, please give first some draft and I give comments on that.

```html
<!DOCTYPE html>
<html lang="en">
<head>
<meta charset="utf-8">
<title>Hope Wings Rally – Mission: Orphan Maria</title>
<link href="https://fonts.googleapis.com/css2?family=Raleway:wght@600;700;800&family=Open+Sans:wght@400;600&family=Mulish:wght@400&display=swap" rel="stylesheet">
<style>
  :root {
    --yellow: #fbb20e;
    --ink: #1c1c1c;
    --bar-dark: #2a2a2a;
    --tab-active: #555555;
    --page-bg: #f2f2f2;
    --card: #ffffff;
    --line: #dddddd;
    --text: #555555;
    --muted: #8a8a8a;
    --track: #d6d6d6;
    --icon-grey: #9a9a9a;
  }
  * { box-sizing: border-box; margin: 0; padding: 0; }
  html, body { width: 1200px; height: 900px; overflow: hidden; }
  body {
    background: var(--page-bg);
    font-family: "Open Sans", sans-serif;
    color: var(--text);
    position: relative;
  }

  /* Header */
  .site-header {
    position: absolute; left: 0; top: 0; width: 1200px; height: 87px;
    background: #000;
  }
  .menu-button {
    position: absolute; left: 36px; top: 20px; width: 47px; height: 47px;
    border: 2px solid var(--yellow); border-radius: 50%;
    display: flex; align-items: center; justify-content: center;
  }
  .nav-link {
    position: absolute; left: 118px; top: 31px;
    font-family: "Raleway", sans-serif; font-weight: 700; font-size: 19px;
    color: #fff; letter-spacing: 0.2px;
  }
  .search-icon { position: absolute; left: 304px; top: 32px; }
  .brand {
    position: absolute; left: 0; width: 1200px; top: 24px; text-align: center;
    font-family: "Raleway", sans-serif; font-weight: 800; font-size: 31px;
    color: #fff; letter-spacing: 0.5px;
  }
  .btn {
    position: absolute; top: 20px; height: 48px;
    font-family: "Raleway", sans-serif; font-weight: 700; font-size: 19px;
    display: flex; align-items: center; justify-content: center; border-radius: 4px;
  }
  .btn-login { left: 921px; width: 110px; border: 1.5px solid #fff; color: var(--yellow); }
  .btn-signup { left: 1055px; width: 107px; background: var(--yellow); color: #fff; }

  /* Share row */
  .share-row { position: absolute; top: 96px; right: 38px; display: flex; gap: 24px; align-items: center; }
  .share-dot { width: 22px; height: 22px; border-radius: 50%; background: var(--icon-grey); }

  /* Cards */
  .card {
    position: absolute; background: var(--card);
    box-shadow: 0 0 0 1px #dcdcdc, 0 2px 3px rgba(0,0,0,0.08);
  }
  .tab-title {
    position: absolute; left: 0; top: 0; height: 40px;
    background: var(--yellow); color: #fff;
    font-family: "Raleway", sans-serif; font-weight: 700; font-size: 22px;
    display: flex; align-items: center; padding-left: 26px;
    clip-path: polygon(0 0, calc(100% - 40px) 0, 100% 100%, 0 100%);
  }
  .tab-rule { position: absolute; left: 0; right: 0; top: 38px; height: 3px; background: var(--yellow); }

  /* Mission card */
  .mission-card { left: 36px; top: 138px; width: 681px; height: 677px; }
  .mission-card .tab-title { width: 462px; top: 0; }
  .mission-tabs {
    position: absolute; left: 0; top: 40px; width: 681px; height: 49px;
    display: flex; background: var(--bar-dark);
  }
  .mission-tab {
    display: flex; align-items: center; justify-content: center;
    font-family: "Raleway", sans-serif; font-weight: 700; font-size: 19px; color: #fff;
  }
  .mission-tab.is-active { background: var(--tab-active); width: 215px; }
  .mission-tab.updates { width: 222px; }
  .mission-tab.comments { width: 244px; }

  .timeline { position: absolute; left: 18px; top: 126px; width: 16px; height: 528px; }
  .timeline-track { position: absolute; left: 3px; top: 8px; width: 10px; height: 512px; background: var(--track); border-radius: 5px; }
  .timeline-node { position: absolute; left: -6px; width: 28px; height: 28px; border-radius: 50%; background: var(--track); }
  .timeline-node.is-current { background: var(--yellow); border: 3px solid #f0d9a0; }

  .story {
    position: absolute; left: 54px; width: 601px;
    font-family: "Mulish", sans-serif; font-size: 16.4px; line-height: 30px; color: #5a5a5a;
  }
  .story-photo {
    position: absolute; left: 54px; top: 287px; width: 601px; height: 190px;
    background: linear-gradient(90deg, #b9a89a 0%, #d7c0a8 30%, #9c8a7e 55%, #c9b2a0 75%, #e6e0dc 100%);
  }

  /* Profile card */
  .profile-card { left: 756px; top: 138px; width: 407px; height: 134px; }
  .profile-card .tab-title { width: 276px; }
  .profile-line {
    position: absolute; left: 20px; display: flex; align-items: center; gap: 12px;
    font-size: 19px; color: #666;
  }

  /* Dark headed cards */
  .panel-head {
    position: absolute; left: 0; top: 0; width: 100%; height: 42px; background: var(--ink);
    color: #fff; font-family: "Raleway", sans-serif; font-weight: 700; font-size: 21px;
    display: flex; align-items: center; padding-left: 18px;
  }
  .support-card { left: 756px; top: 298px; width: 407px; height: 208px; }
  .supporters { position: absolute; right: 52px; top: 8px; display: flex; gap: 5px; }
  .supporter { width: 29px; height: 29px; border-radius: 50%; background: #bdbdbd; border: 2px solid #fff; overflow: hidden; }
  .panel-next {
    position: absolute; right: 0; top: 0; width: 30px; height: 42px; background: #000;
    display: flex; align-items: center; justify-content: center;
  }
  .support-now { position: absolute; left: 17px; top: 54px; font-size: 19px; font-weight: 600; color: #666; }
  .ring { position: absolute; left: 775px; top: 394px; }
  .given { position: absolute; left: 906px; top: 392px; font-size: 21px; font-weight: 600; color: #555; }
  .given-note { position: absolute; left: 906px; top: 422px; font-size: 16px; color: #777; }
  .per-month { position: absolute; left: 906px; top: 452px; display: flex; align-items: center; gap: 10px; font-size: 19px; font-weight: 600; color: #666; }

  .participate-card { left: 756px; top: 532px; width: 407px; height: 283px; }
  .options { position: absolute; left: 0; top: 42px; width: 100%; list-style: none; }
  .option {
    height: 47.5px; display: flex; align-items: center; padding: 0 20px;
    border-bottom: 1px solid var(--line); font-size: 17.5px; color: #666;
  }
  .option:last-child { border-bottom: none; }
  .checkbox { width: 17px; height: 17px; border: 1.5px solid #777; border-radius: 3px; margin-right: 14px; flex: none; }
  .option-label { flex: 1; }
  .amount-input {
    width: 171px; height: 34px; border: 1px solid #ccc; border-radius: 4px;
    font-size: 15px; color: #666; padding-left: 12px; display: flex; align-items: center; margin: 0 28px 0 16px;
  }

  .site-footer {
    position: absolute; left: 0; width: 1200px; top: 848px; text-align: center;
    font-size: 16.5px; color: #444;
  }
</style>
</head>
<body>

<header class="site-header">
  <div class="menu-button">
    <svg width="18" height="14" viewBox="0 0 18 14"><rect y="0" width="18" height="2.6" rx="1" fill="#fbb20e"/><rect y="5.7" width="18" height="2.6" rx="1" fill="#fbb20e"/><rect y="11.4" width="18" height="2.6" rx="1" fill="#fbb20e"/></svg>
  </div>
  <div class="nav-link">SEE THE MISSION</div>
  <svg class="search-icon" width="24" height="24" viewBox="0 0 24 24"><circle cx="10" cy="10" r="7" fill="none" stroke="#fff" stroke-width="3"/><line x1="15" y1="15" x2="21.5" y2="21.5" stroke="#fff" stroke-width="3.5" stroke-linecap="round"/></svg>
  <div class="brand">HOPE WINGS RALLY</div>
  <div class="btn btn-login">LOGIN</div>
  <div class="btn btn-signup">SIGN UP</div>
</header>

<div class="share-row">
  <svg width="30" height="22" viewBox="0 0 30 22"><path d="M2 3 Q8 1 15 4 Q22 1 28 3 V20 Q22 18 15 21 Q8 18 2 20 Z M15 4 V21" fill="none" stroke="#9a9a9a" stroke-width="2"/></svg>
  <span class="share-dot"></span>
  <span class="share-dot"></span>
  <span class="share-dot"></span>
</div>

<section class="card mission-card">
  <div class="tab-rule"></div>
  <h1 class="tab-title">MISSION : ORPHAN MARIA, 11Y</h1>
  <nav class="mission-tabs">
    <div class="mission-tab is-active">STORY</div>
    <div class="mission-tab updates">UPDATES</div>
    <div class="mission-tab comments">COMMENTS</div>
  </nav>
  <div class="timeline">
    <div class="timeline-track"></div>
    <div class="timeline-node" style="top:0"></div>
    <div class="timeline-node is-current" style="top:254px"></div>
    <div class="timeline-node" style="top:500px"></div>
  </div>
  <p class="story" style="top:114px">At vero eos et accusamus et iusto odio dignissimos ducimus qui blanditiis prae sentium voluptatum deleniti atque corrupti quos dolores et quas molestiaexce pturi sint occaecati cupiditate non provident, similique sunt in culpa qui officia deserunt mollitia animi, id est laborum et dolorum fuga. Et harum quidem rer um facilis est et expedita distinctio.</p>
  <div class="story-photo" role="img" aria-label="Photo of a row of schoolchildren singing together in class"></div>
  <p class="story" style="top:500px">em quibusdam et aut officiis debitis aut rerum necessitatibus saepe eveniet ut et voluptates repudiandae sint et molestiae non recusandae. Itaque earurerm hic tenetur a sapiente delectus, ut aut reiciendis voluptatibus maiores alias cns equatur aut perferendis doloribus asperiores repellat sed quia non numquam eius modi tempora incidunt ut labore et.</p>
</section>

<aside class="card profile-card">
  <div class="tab-rule" style="top:39px"></div>
  <h2 class="tab-title" style="height:41px">NAME: MARIA, 11Y</h2>
  <div class="profile-line" style="top:58px">
    <svg width="12" height="17" viewBox="0 0 12 17"><path d="M6 0 C2.7 0 0 2.6 0 5.9 C0 10 6 17 6 17 C6 17 12 10 12 5.9 C12 2.6 9.3 0 6 0 Z" fill="#fbb20e"/><circle cx="6" cy="6" r="2.3" fill="#fff"/></svg>
    <span>Kalkutta</span>
  </div>
  <div class="profile-line" style="top:95px">
    <svg width="17" height="17" viewBox="0 0 17 17"><circle cx="8.5" cy="8.5" r="8.5" fill="#fbb20e"/><path d="M4 4 Q7 5 6 8 Q9 9 8 12 M11 3 Q10 6 13 8" fill="none" stroke="#fff" stroke-width="1.5"/></svg>
    <span>Oranization : Jacob</span>
  </div>
</aside>

<section class="card support-card">
  <div class="panel-head">Support</div>
  <div class="supporters">
    <span class="supporter"><svg width="25" height="25" viewBox="0 0 25 25"><circle cx="12.5" cy="10" r="5" fill="#fff"/><path d="M3 25 Q12.5 13 22 25 Z" fill="#fff"/></svg></span>
    <span class="supporter"><svg width="25" height="25" viewBox="0 0 25 25"><circle cx="12.5" cy="10" r="5" fill="#fff"/><path d="M3 25 Q12.5 13 22 25 Z" fill="#fff"/></svg></span>
    <span class="supporter"><svg width="25" height="25" viewBox="0 0 25 25"><circle cx="12.5" cy="10" r="5" fill="#fff"/><path d="M3 25 Q12.5 13 22 25 Z" fill="#fff"/></svg></span>
    <span class="supporter"><svg width="25" height="25" viewBox="0 0 25 25"><circle cx="12.5" cy="10" r="5" fill="#fff"/><path d="M3 25 Q12.5 13 22 25 Z" fill="#fff"/></svg></span>
    <span class="supporter"><svg width="25" height="25" viewBox="0 0 25 25"><circle cx="12.5" cy="10" r="5" fill="#fff"/><path d="M3 25 Q12.5 13 22 25 Z" fill="#fff"/></svg></span>
  </div>
  <div class="panel-next"><svg width="10" height="16" viewBox="0 0 10 16"><path d="M2 2 L8 8 L2 14" fill="none" stroke="#fbb20e" stroke-width="2.6"/></svg></div>
  <div class="support-now">My Support is now: $5/Month</div>
</section>
<svg class="ring" width="100" height="100" viewBox="0 0 100 100">
  <circle cx="50" cy="50" r="44" fill="none" stroke="#8c8c8c" stroke-width="7"/>
  <circle cx="50" cy="50" r="44" fill="none" stroke="#fbb20e" stroke-width="7" stroke-dasharray="124.4 276.5" transform="rotate(-90 50 50)"/>
  <text x="50" y="58" text-anchor="middle" font-family="Open Sans, sans-serif" font-size="22" font-weight="600" fill="#555">45%</text>
</svg>
<div class="given">$15 Given</div>
<div class="given-note">of total $35 needed</div>
<div class="per-month">
  <svg width="18" height="18" viewBox="0 0 18 18"><rect x="1" y="3" width="16" height="14" rx="1.5" fill="none" stroke="#fbb20e" stroke-width="2"/><rect x="1" y="3" width="16" height="4" fill="#fbb20e"/><rect x="4" y="0" width="2" height="4" fill="#fbb20e"/><rect x="12" y="0" width="2" height="4" fill="#fbb20e"/><g fill="#fbb20e"><rect x="4" y="9" width="2.5" height="2.5"/><rect x="8" y="9" width="2.5" height="2.5"/><rect x="12" y="9" width="2.5" height="2.5"/><rect x="4" y="13" width="2.5" height="2.5"/><rect x="8" y="13" width="2.5" height="2.5"/></g></svg>
  <span>Per month needed</span>
</div>

<section class="card participate-card">
  <div class="panel-head">Participate</div>
  <ul class="options">
    <li class="option"><span class="checkbox"></span><span class="option-label">Iam in, $1/month</span><svg width="22" height="20" viewBox="0 0 22 20"><path d="M0 1 H4 L7 13 H19 L22 4 H6" fill="#fbb20e" stroke="#fbb20e" stroke-width="2" stroke-linejoin="round"/><circle cx="8.5" cy="17.5" r="2" fill="#fbb20e"/><circle cx="17.5" cy="17.5" r="2" fill="#fbb20e"/></svg></li>
    <li class="option"><span class="checkbox"></span><span class="option-label">Increased, $5/month</span><svg width="22" height="20" viewBox="0 0 22 20"><path d="M0 1 H4 L7 13 H19 L22 4 H6" fill="#fbb20e" stroke="#fbb20e" stroke-width="2" stroke-linejoin="round"/><circle cx="8.5" cy="17.5" r="2" fill="#fbb20e"/><circle cx="17.5" cy="17.5" r="2" fill="#fbb20e"/></svg></li>
    <li class="option"><span class="checkbox"></span><span class="option-label">Decent help, $10/month</span><svg width="22" height="20" viewBox="0 0 22 20"><path d="M0 1 H4 L7 13 H19 L22 4 H6" fill="#fbb20e" stroke="#fbb20e" stroke-width="2" stroke-linejoin="round"/><circle cx="8.5" cy="17.5" r="2" fill="#fbb20e"/><circle cx="17.5" cy="17.5" r="2" fill="#fbb20e"/></svg></li>
    <li class="option"><span class="checkbox"></span><span class="option-label">Whole kid, $35/month</span><svg width="22" height="20" viewBox="0 0 22 20"><path d="M0 1 H4 L7 13 H19 L22 4 H6" fill="#fbb20e" stroke="#fbb20e" stroke-width="2" stroke-linejoin="round"/><circle cx="8.5" cy="17.5" r="2" fill="#fbb20e"/><circle cx="17.5" cy="17.5" r="2" fill="#fbb20e"/></svg></li>
    <li class="option"><span class="checkbox"></span><span>My Amount</span><span class="amount-input">Enter Amount</span><svg width="22" height="20" viewBox="0 0 22 20"><path d="M0 1 H4 L7 13 H19 L22 4 H6" fill="#fbb20e" stroke="#fbb20e" stroke-width="2" stroke-linejoin="round"/><circle cx="8.5" cy="17.5" r="2" fill="#fbb20e"/><circle cx="17.5" cy="17.5" r="2" fill="#fbb20e"/></svg></li>
  </ul>
</section>

<footer class="site-footer">Copyrights © 2016, Hope Wings Rally. All rights reserved.</footer>

</body>
</html>
```